Verlindo Magician

I want the business card for my business to give to people who watch that later I will be employed to show magic here is my website http://www.balsamomagicien.com/I want the interesting design , i am very opened for formal and informal, I watch a lot of design so don't stick to the common shape and form but i hope it can also be produced the thing to write on will be the same as in picture that i will upload , i also will upload the logo for you that so can be easy to useDenis CostilleMagicianMAGICIAN VERLINDO 17 rue des Tilleuls - 25000 BESANÇON contact@verlindoillusions.example tel. 0381 946 157 tel. 0674 219 503

```html
<!DOCTYPE html>
<html lang="fr">
<head>
<meta charset="utf-8">
<title>Verlindo Magician – Business Card</title>
<link href="https://fonts.googleapis.com/css2?family=Montserrat:wght@400;500;700&display=swap" rel="stylesheet">
<style>
  :root {
    --stage: #e9e6e1;
    --card-dark: #1f1f20;
    --card-light: #ffffff;
    --accent-red: #e8262b;
    --text-light: #e6e6e6;
    --text-dark: #1b1b1b;
    --rule: #6a6a6a;
    --figure-dark: #0e0e0e;
    --figure-light: #f1f1f1;
  }
  * { box-sizing: border-box; margin: 0; padding: 0; }
  html, body {
    width: 1200px; height: 768px; overflow: hidden;
    background: var(--stage);
    font-family: "Montserrat", sans-serif;
  }
  .stage {
    width: 1200px; height: 768px;
    display: flex; align-items: center; justify-content: center; gap: 80px;
  }
  .card {
    width: 400px; height: 620px;
    border-radius: 26px;
    position: relative;
    overflow: hidden;
    box-shadow: 0 10px 30px rgba(0,0,0,.18);
  }

  /* Front: contact side */
  .card--front {
    background: var(--card-dark);
    color: var(--text-light);
    text-align: center;
    padding-top: 52px;
  }
  .card__name {
    color: var(--accent-red);
    font-weight: 500;
    font-size: 34px;
    letter-spacing: 1px;
    text-transform: uppercase;
  }
  .card__role {
    margin-top: 6px;
    font-size: 15px;
    letter-spacing: 2px;
    color: var(--text-light);
  }
  .card__role .suit { font-size: 14px; }
  .card__divider {
    margin: 18px auto 0;
    width: 300px;
    display: flex; align-items: center; gap: 10px;
  }
  .card__divider::before, .card__divider::after {
    content: ""; flex: 1; height: 1px; background: var(--rule);
  }
  .contact-icons { display: flex; gap: 6px; }
  .contact-icons__item {
    width: 24px; height: 24px; border-radius: 50%;
    background: var(--accent-red);
    display: flex; align-items: center; justify-content: center;
  }
  .contact-icons__item svg { width: 14px; height: 14px; }
  .card__details {
    margin-top: 18px;
    font-size: 14px;
    line-height: 1.55;
    letter-spacing: .3px;
  }
  .card__details .business { text-transform: uppercase; letter-spacing: 1px; }
  .card__portrait {
    position: absolute; left: 90px; bottom: 34px;
    width: 220px; height: 200px;
    border-radius: 90px 90px 10px 10px;
    background: linear-gradient(180deg, #2a2a2a 0%, var(--figure-dark) 100%);
    border: 2px solid var(--figure-light);
  }

  /* Back: brand side */
  .card--back {
    background: radial-gradient(circle at 50% 45%, #ffffff 0%, #f7f4f4 100%);
    display: flex; flex-direction: column; align-items: center;
    padding-top: 150px;
  }
  .card--back .card__portrait {
    position: static;
    width: 240px; height: 210px;
    border: none;
    background: linear-gradient(180deg, #3a3a3a 0%, var(--figure-dark) 100%);
  }
  .brand {
    margin-top: 10px;
    display: flex; flex-direction: column; align-items: center;
    color: var(--text-dark);
  }
  .brand__name {
    font-weight: 400;
    font-size: 44px;
    letter-spacing: 4px;
  }
  .brand__tag {
    font-size: 11px;
    letter-spacing: 2px;
    color: var(--text-dark);
  }
</style>
</head>
<body>
<main class="stage">

  <article class="card card--front">
    <h1 class="card__name">Marc Ravoulet</h1>
    <p class="card__role"><span class="suit">♠♦</span> MAGICIEN <span class="suit">♥♣</span></p>

    <div class="card__divider">
      <div class="contact-icons">
        <span class="contact-icons__item" aria-label="Adresse">
          <svg viewBox="0 0 24 24" fill="#fff"><path d="M12 2a7 7 0 0 0-7 7c0 5 7 13 7 13s7-8 7-13a7 7 0 0 0-7-7zm0 9.5a2.5 2.5 0 1 1 0-5 2.5 2.5 0 0 1 0 5z"/></svg>
        </span>
        <span class="contact-icons__item" aria-label="Téléphone">
          <svg viewBox="0 0 24 24" fill="#fff"><path d="M6.6 10.8a15 15 0 0 0 6.6 6.6l2.2-2.2c.3-.3.7-.4 1-.2 1.1.4 2.3.6 3.6.6.6 0 1 .4 1 1V20c0 .6-.4 1-1 1A17 17 0 0 1 3 4c0-.6.4-1 1-1h3.5c.6 0 1 .4 1 1 0 1.3.2 2.5.6 3.6.1.3 0 .7-.2 1z"/></svg>
        </span>
        <span class="contact-icons__item" aria-label="E-mail">
          <svg viewBox="0 0 24 24" fill="none" stroke="#fff" stroke-width="2"><rect x="3" y="5" width="18" height="14" rx="1"/><path d="M3 6l9 7 9-7"/></svg>
        </span>
        <span class="contact-icons__item" aria-label="Site web">
          <svg viewBox="0 0 24 24" fill="none" stroke="#fff" stroke-width="2"><circle cx="12" cy="12" r="9"/><path d="M3 12h18M12 3c3 3.5 3 14.5 0 18M12 3c-3 3.5-3 14.5 0 18"/></svg>
        </span>
      </div>
    </div>

    <div class="card__details">
      <p class="business">Magician Verlindo</p>
      <p>17 rue des Tilleuls - 25000 BESANÇON</p>
      <p>0381 946 157 | 0674 219 503</p>
      <p>contact@verlindoillusions.example</p>
      <p>www.verlindoillusions.example</p>
    </div>

    <div class="card__portrait" role="img" aria-label="Illustration of the magician in a black jacket holding a playing card"></div>
  </article>

  <article class="card card--back">
    <div class="card__portrait" role="img" aria-label="Illustration of the magician in a black jacket holding a playing card"></div>
    <div class="brand">
      <span class="brand__name">VERLINDO</span>
      <span class="brand__tag">MAGICIEN</span>
    </div>
  </article>

</main>
</body>
</html>
```